Marwick Family Chiropractic Stationary

The letterhead and business card must have our logo.
We would like to see the logo used in different ways ( It can be expanded upon in the stationary.)
Please use the the same or similar colors.
Must be eye catching and memorable.
Must be easy to read

Reason: The doctor has been too busy to make any final decisions. He would like to give himself a little more time.

Target Market(s)

Chiropractic Healthcare

Industry/Entity Type

Business

Requirements
Must have
• Dr. Leonard Marwick D.C.
Chiropractor

860-555-0183

417 Birchfield Road, 2nd Floor
Ashford Mills, CT 06091

drmarwick@marwickspine.example
www.marwickspine.example
www.facebook.com/MarwickFamilySpine
Should not have
• should not be difficult to read

```html
<!DOCTYPE html>
<html lang="en">
<head>
<meta charset="utf-8">
<title>Marwick Family Chiropractic – Envelope</title>
<link rel="stylesheet" href="https://fonts.googleapis.com/css2?family=Montserrat:wght@700&family=Open+Sans:ital,wght@0,400;0,700;1,400;1,700&display=swap">
<style>
  :root {
    --backdrop: #ececec;
    --paper: #ffffff;
    --leaf-green: #3c9a1c;
    --leaf-light: #8cc63f;
    --leaf-olive: #a39a1e;
    --bark: #3a332c;
    --ink: #3a3a3a;
    --label-grey: #b4b4b4;
    --ghost-grey: #dcdcdc;
  }
  * { box-sizing: border-box; margin: 0; padding: 0; }
  html, body { width: 1200px; height: 868px; overflow: hidden; }
  body {
    background: var(--backdrop);
    font-family: "Open Sans", Arial, sans-serif;
    position: relative;
  }

  .presentation-label {
    position: absolute;
    left: 54px;
    top: 44px;
    color: var(--label-grey);
  }
  .presentation-label .label-title {
    font-weight: 700;
    font-size: 20px;
    letter-spacing: 1px;
    margin-bottom: 24px;
  }
  .presentation-label .label-client {
    font-style: italic;
    font-size: 17px;
    line-height: 23px;
    margin-bottom: 22px;
  }
  .presentation-label .label-variant {
    font-style: italic;
    font-weight: 700;
    font-size: 17px;
  }

  .envelope {
    position: absolute;
    background: var(--paper);
    box-shadow: 0 6px 18px rgba(0,0,0,0.12);
    overflow: hidden;
  }

  /* Back of envelope */
  .envelope-back {
    left: 560px;
    top: 90px;
    width: 560px;
    height: 280px;
  }
  .envelope-back .flap {
    position: absolute;
    left: 0; top: 0;
    width: 100%;
    height: 104px;
    background: var(--bark);
    border-radius: 0 0 10px 10px;
    display: flex;
    flex-direction: column;
    align-items: center;
    justify-content: center;
    gap: 8px;
  }
  .flap .flap-mark {
    display: flex;
    align-items: center;
    gap: 6px;
    font-family: "Montserrat", Arial, sans-serif;
    font-weight: 700;
    font-size: 10px;
    letter-spacing: 0.5px;
    color: var(--leaf-light);
    text-transform: uppercase;
  }
  .flap .flap-mark .dot {
    width: 8px; height: 8px;
    border-radius: 50%;
    background: var(--leaf-light);
  }
  .flap .flap-web {
    font-size: 8px;
    color: #9a948c;
    letter-spacing: 0.3px;
  }
  .envelope-back .ghost-name {
    position: absolute;
    left: 0; right: 0;
    top: 170px;
    text-align: center;
    color: var(--ghost-grey);
    font-family: "Montserrat", Arial, sans-serif;
    font-weight: 700;
    line-height: 1.1;
  }
  .ghost-name .ghost-main { font-size: 24px; letter-spacing: 2px; }
  .ghost-name .ghost-sub { font-size: 10px; letter-spacing: 2px; }

  /* Front of envelope */
  .envelope-front {
    left: 70px;
    top: 470px;
    width: 640px;
    height: 320px;
  }
  .envelope-front .brand {
    position: absolute;
    left: 40px;
    top: 36px;
    display: flex;
    align-items: center;
    gap: 8px;
    font-family: "Montserrat", Arial, sans-serif;
    font-weight: 700;
    font-size: 15px;
    color: var(--leaf-green);
    text-transform: uppercase;
    letter-spacing: 0.5px;
  }
  .brand .dot {
    width: 14px; height: 14px;
    border-radius: 50%;
    background: var(--leaf-green);
  }
  .envelope-front .return-address {
    position: absolute;
    left: 40px;
    top: 112px;
    font-size: 10px;
    line-height: 14px;
    color: var(--ink);
    font-style: normal;
  }
  .envelope-front .tree-art {
    position: absolute;
    right: 0;
    bottom: 30px;
    width: 210px;
    height: 200px;
    background:
      radial-gradient(ellipse 50% 50% at 55% 42%,
        rgba(140,198,63,0.75) 0%,
        rgba(163,154,30,0.45) 50%,
        rgba(255,255,255,0) 100%);
  }
  .envelope-front .ground-band {
    position: absolute;
    left: 0; bottom: 0;
    width: 100%;
    height: 40px;
  }
</style>
</head>
<body>

  <header class="presentation-label">
    <p class="label-title">ENVELOPE</p>
    <p class="label-client">Marwick Family<br>Chiropractic</p>
    <p class="label-variant">Variant 1</p>
  </header>

  <section class="envelope envelope-back" aria-label="Envelope back">
    <div class="flap">
      <div class="flap-mark"><span class="dot"></span>Marwick Family Chiropractic</div>
      <div class="flap-web">www.marwickspine.example</div>
    </div>
    <div class="ghost-name">
      <div class="ghost-main">MARWICK</div>
      <div class="ghost-sub">FAMILY CHIROPRACTIC</div>
    </div>
  </section>

  <section class="envelope envelope-front" aria-label="Envelope front">
    <div class="brand"><span class="dot"></span>Marwick Family Chiropractic</div>
    <address class="return-address">
      417 Birchfield Road, 2nd Floor,<br>
      Ashford Mills, CT 06091
    </address>
    <div class="tree-art" role="img" aria-label="Illustration of a tree with scattered green and olive leaves rising from the ground band"></div>
    <svg class="ground-band" viewBox="0 0 640 40" preserveAspectRatio="none" aria-hidden="true">
      <rect x="0" y="30" width="640" height="10" fill="var(--leaf-green)"/>
      <path d="M440 30 C500 14 570 8 640 6 L640 40 L440 40 Z" fill="var(--leaf-green)"/>
    </svg>
  </section>

</body>
</html>
```